Company or website name
- Velmira, LLC
- Velmira, LLC
- Describe your company and organization and target audience
- Velmira, LLC is a research, science and technology based manufacturing company that formulates, develops, manufactures and packages a full complement of personal care products for domestic and international concerns. We private label and contract package personal care products, cosmetics, bath salts and powders and home fragrance products. Velmira is conveniently located in Southern California adjacent to major transportation hubs and international airports. We utilize earth friendly, green manufacturing processes, maximize the use of renewable resource raw materials and minimize the use of non-renewable and petrochemical based raw materials. We provide formulation and product development services with low minimum order quantities and short lead times. Velmira is the intersection between nature, science, beauty and innovation. We are a B-2-B company.
- The design should have the following
- We're looking for an ad design that can be used for both banner and column use online and in print. We manufacture bath and body products such as bath salts, body washes, body powders, bath oils and bubble baths, hair care products such as shampoos, conditioners and styling aids, skin care products such as anti-aging creams, cleansers, masks, toners and serums, color cosmetics such as eyeliners, mascaras, foundations and mineral make-up powders, manicure/pedicure products such as cuticle oils, sugar and salt scrubs and foot soaks/softeners and spa products such as seaweed wraps, cellulite creams, body masks, massage oils and candles. Our strengths are natural and organic product formulation, low minimums, competitive prices, complete research &development services new and innovative ingredients and fast turnaround times. Examples can be found at the following sites: http://www.glintor.com/ http://www.grovewellboard.org/ http://www.tessaloomjournal.com/ http://nerwast.org/images/downloads/bulletins/2009-10-bulletin.pdf http://www.pantrykestrelworks.com/

```html
<!DOCTYPE html>
<html lang="en">
<head>
<meta charset="utf-8">
<title>Velmira Print Ad Sizes</title>
<link rel="stylesheet" href="https://fonts.googleapis.com/css2?family=Arimo:wght@700&family=Kreon:wght@300;400&family=Open+Sans:wght@400;600;700&display=swap">
<style>
:root{
  --board:#000;
  --paper:#fff;
  --teal:#2b7f86;
  --teal-head:#3a8a8c;
  --ink:#333;
  --gold:#c9a24a;
  --photo-deep:#0c2d3c;
  --photo-mid:#1f6b7c;
  --photo-band:#1c5c6a;
  --photo-cyan:#5fc4d6;
  --photo-red:#c8242b;
}
*{margin:0;padding:0;box-sizing:border-box}
html,body{width:1200px;height:986px;overflow:hidden;background:var(--board)}
.board{position:relative;width:1200px;height:986px;background:var(--board);font-family:"Open Sans",sans-serif;color:var(--ink)}
.board-title{position:absolute;right:56px;top:24px;font:700 33px "Arimo",sans-serif;color:#fff;letter-spacing:.5px}
.size-label{position:absolute;font:700 14px "Arimo",sans-serif;color:#fff;white-space:nowrap}
.size-label small{display:block;font:400 11px "Arimo",sans-serif;margin-top:1px}
.ad{position:absolute;background:var(--paper);overflow:hidden}
.photo{position:absolute;left:0;top:0;width:100%;
  background:
    radial-gradient(circle at 78% 52%, var(--photo-red) 0, rgba(200,36,43,.55) 9%, rgba(200,36,43,0) 20%),
    radial-gradient(ellipse at 40% 25%, var(--photo-cyan) 0, rgba(95,196,214,.4) 22%, rgba(95,196,214,0) 45%),
    linear-gradient(180deg, var(--photo-mid) 0%, var(--photo-deep) 45%, #123c4c 70%, var(--photo-band) 100%)}
.headline{position:absolute;font-family:"Kreon",serif;font-weight:300;color:#fff;line-height:1.12}
.brand{position:absolute;display:flex;align-items:center;gap:3px;font-family:"Kreon",serif;font-weight:400;color:var(--gold)}
.brand .dot{border-radius:50%;background:var(--gold)}
.body{position:absolute;line-height:1.4}
.body p{margin-bottom:.7em}
.cat{font-weight:700;color:var(--teal)}
.items{margin-bottom:.45em}
.products{position:absolute;background:linear-gradient(135deg,#f3d9a8,#b8743a 45%,#e7c9b4 75%,#f6e6d8)}
.flower{position:absolute;background:linear-gradient(135deg,#f0dcae,#c9a24a)}
.rule{position:absolute;height:1px;background:#9cc7c9}
.address{position:absolute;line-height:1.4}
.address b{color:var(--teal);font-weight:700}
.short-list{position:absolute;font-weight:700;color:var(--teal);line-height:1.35}
.cols{display:flex;gap:12px}
.cols > div{flex:1;white-space:nowrap}
</style>
</head>
<body>
<div class="board">
  <div class="board-title">PRINT AD</div>

  <div class="size-label" style="left:101px;top:73px">Full Page : 8.25” x 11.125</div>
  <div class="size-label" style="left:524px;top:73px">2/3 Page Vertical : 5.25” x 11.125”<small>(Two Columns)</small></div>
  <div class="size-label" style="left:815px;top:73px">1/3 Page Vertical : 2.875” x 11.125”<small>(One Column)</small></div>
  <div class="size-label" style="left:101px;top:643px">1/1 Page : 5.5” x 5.5</div>
  <div class="size-label" style="left:390px;top:643px">1/2 Spread Horizontal : 16.25” x 5.5</div>

  <!-- Full page -->
  <section class="ad ad-full" style="left:103px;top:111px;width:359px;height:485px">
    <div class="photo" style="height:255px" role="img" aria-label="Lab scientist in cap, mask and goggles holding a test tube"></div>
    <div class="brand" style="right:14px;top:16px;font-size:22px"><span class="dot" style="width:9px;height:9px"></span>Velmira</div>
    <div class="headline" style="left:40px;top:184px;font-size:26px">A stay with us<br>Will change your life</div>
    <div class="body" style="left:40px;top:272px;width:292px;font-size:6.2px">
      <p>Velmira, LLC is a research, science and technology based manufacturing company that formulates, develops, manufactures and packages a full complement of personal care products for domestic and international concerns. We private label and contract package personal care products, cosmetics, bath salts and powders and home fragrance products.</p>
      <p>Our strengths are natural and organic product formulation, low minimums, competitive prices, complete research &amp; development services new and innovative ingredients and fast turnaround times.</p>
      <div style="font-size:5.3px;margin-top:10px">
        <div class="cat">Bath &amp; Body Products</div><div class="items">Bath Salts • Body Washes • Body Powders • Bath Oils • Bubble Baths</div>
        <div class="cat">Hair Care Products</div><div class="items">Shampoos • Conditioners • Styling Aids</div>
        <div class="cat">Skin Care Products</div><div class="items">Anti-aging Creams • Cleansers • Masks • Toners • Serums</div>
        <div class="cat">Color Cosmetics</div><div class="items">Eyeliners • Mascaras • Foundations • Mineral Make-up Powders</div>
        <div class="cat">Manicure / Pedicure</div><div class="items">Cuticle Oils • Sugar • Salt Scrubs • Foot Soaks • Softeners</div>
        <div class="cat">Spa Products</div><div class="items">Seaweed Wraps • Cellulite Creams • Body Masks • Massage Oils • Candles</div>
      </div>
    </div>
    <div class="products" style="left:238px;top:400px;width:92px;height:52px" role="img" aria-label="Spa products: bottles, soaps, towel and flowers"></div>
    <div class="rule" style="left:40px;top:456px;width:290px"></div>
    <div class="address" style="left:40px;top:459px;font-size:5.5px">4120 W. Larkspur Avenue, Building 210, Fullerton, CA 92833<br><b>P</b> 555.302.4100 &nbsp;|&nbsp; <b>F</b> 555.302.4101 &nbsp;|&nbsp; <b>E</b> info@velmira.com</div>
    <div class="flower" style="right:0;bottom:0;width:44px;height:36px" role="img" aria-label="Gold hibiscus flower decoration"></div>
  </section>

  <!-- 2/3 page -->
  <section class="ad ad-two-thirds" style="left:524px;top:111px;width:229px;height:485px">
    <div class="photo" style="height:245px" role="img" aria-label="Lab scientist in cap, mask and goggles holding a test tube"></div>
    <div class="brand" style="right:12px;top:14px;font-size:17px"><span class="dot" style="width:7px;height:7px"></span>Velmira</div>
    <div class="headline" style="left:17px;top:200px;font-size:17.5px">A stay with us<br>Will change your life</div>
    <div class="body" style="left:17px;top:256px;width:200px;font-size:5.3px">
      <p>Velmira, LLC is a research, science and technology based manufacturing company that formulates, develops, manufactures and packages a full complement of personal care products for domestic and international concerns. We private label and contract package personal care products, cosmetics, bath salts and powders and home fragrance products.</p>
      <p>Our strengths are natural and organic product formulation, low minimums, competitive prices, complete research &amp; development services new and innovative ingredients and fast turnaround times.</p>
      <div style="font-size:4.9px;margin-top:8px">
        <div class="cat">Bath &amp; Body Products</div><div class="items">Bath Salts • Body Washes • Body Powders • Bath Oils • Bubble Baths</div>
        <div class="cat">Hair Care Products</div><div class="items">Shampoos • Conditioners • Styling Aids</div>
        <div class="cat">Skin Care Products</div><div class="items">Anti-aging Creams • Cleansers • Masks • Toners • Serums</div>
        <div class="cat">Color Cosmetics</div><div class="items">Eyeliners • Mascaras • Foundations • Mineral Make-up Powders</div>
        <div class="cat">Manicure / Pedicure</div><div class="items">Cuticle Oils • Sugar • Salt Scrubs • Foot Soaks<br>Softeners</div>
        <div class="cat">Spa Products</div><div class="items">Seaweed Wraps • Cellulite Creams • Body Masks<br>Massage Oils • Candles</div>
      </div>
    </div>
    <div class="products" style="left:150px;top:410px;width:66px;height:50px" role="img" aria-label="Spa products: bottles, soaps, towel and flowers"></div>
    <div class="rule" style="left:17px;top:462px;width:200px"></div>
    <div class="address" style="left:17px;top:464px;font-size:5px">4120 W. Larkspur Avenue, Building 210, Fullerton, CA 92833<br><b>P</b> 555.302.4100 | <b>F</b> 555.302.4101 | <b>E</b> info@velmira.com</div>
    <div class="flower" style="right:0;bottom:0;width:36px;height:28px" role="img" aria-label="Gold hibiscus flower decoration"></div>
  </section>

  <!-- 1/3 page -->
  <section class="ad ad-one-third" style="left:816px;top:111px;width:125px;height:485px">
    <div class="photo" style="height:217px" role="img" aria-label="Lab scientist in cap, mask and goggles holding a test tube"></div>
    <div class="headline" style="left:12px;top:162px;font-size:13.5px;line-height:1.1">A stay with us<br>Will change your life</div>
    <div class="body" style="left:12px;top:225px;width:104px;font-size:4.4px;text-align:justify">
      <p>Natural and organic product formulation, low minimums, competitive prices, complete research &amp; development services new and innovative ingredients &amp; fast turnaround times.</p>
      <div style="font-size:4.3px;margin-top:5px;text-align:left">
        <div class="cat">Bath &amp; Body Products</div><div class="items">Bath Salts • Body Washes • Body Powders<br>Bath Oils • Bubble Baths</div>
        <div class="cat">Hair Care Products</div><div class="items">Shampoos • Conditioners • Styling Aids</div>
        <div class="cat">Skin Care Products</div><div class="items">Anti-aging Creams • Cleansers • Masks<br>Toners • Serums</div>
        <div class="cat">Color Cosmetics</div><div class="items">Eyeliners • Mascaras • Foundations<br>Mineral Make-up Powders</div>
        <div class="cat">Manicure / Pedicure</div><div class="items">Cuticle Oils • Sugar • Salt Scrubs<br>Foot Soaks • Softeners</div>
        <div class="cat">Spa Products</div><div class="items">Seaweed Wraps<br>Cellulite Creams<br>Body Masks<br>Massage Oils<br>Candles</div>
      </div>
    </div>
    <div class="products" style="left:58px;top:384px;width:58px;height:40px" role="img" aria-label="Spa products: bottles, soaps, towel and flowers"></div>
    <div class="rule" style="left:10px;top:428px;width:106px"></div>
    <div class="brand" style="left:18px;top:432px;font-size:19px"><span class="dot" style="width:7px;height:7px"></span>Velmira</div>
    <div class="address" style="left:8px;top:464px;width:110px;font-size:3.6px;text-align:center">4120 W. Larkspur Avenue, Building 210<br>Fullerton, CA 92833<br><b>P</b> 555.302.4100 | <b>F</b> 555.302.4101 | <b>E</b> info@velmira.com</div>
  </section>

  <!-- 1/1 page -->
  <section class="ad ad-square" style="left:103px;top:672px;width:239px;height:239px">
    <div class="photo" style="height:164px" role="img" aria-label="Lab scientist in cap, mask and goggles holding a test tube"></div>
    <div class="brand" style="right:10px;top:10px;font-size:17px"><span class="dot" style="width:7px;height:7px"></span>Velmira</div>
    <div class="headline" style="left:20px;top:110px;font-size:18px">A stay with us<br>Will change your life</div>
    <div class="short-list" style="left:20px;top:171px;font-size:7px">Bath &amp; Body Care &nbsp;•&nbsp; Hair Care<br>Skin Care &nbsp;•&nbsp; Color Cosmetics<br>Manicure / Pedicure &nbsp;•&nbsp; Spa</div>
    <div class="products" style="left:150px;top:166px;width:70px;height:38px" role="img" aria-label="Spa products: bottles, soaps, towel and flowers"></div>
    <div class="rule" style="left:20px;top:207px;width:210px"></div>
    <div class="address" style="left:20px;top:209px;font-size:5.6px">4120 W. Larkspur Avenue,<br>Building 210, Fullerton, CA 92833.<br><b>P</b> 555.302.4100 &nbsp;|&nbsp; <b>F</b> 555.302.4101 &nbsp;|&nbsp; <b>E</b> info@velmira.com</div>
    <div class="flower" style="right:0;bottom:0;width:30px;height:26px" role="img" aria-label="Gold hibiscus flower decoration"></div>
  </section>

  <!-- 1/2 spread -->
  <section class="ad ad-spread" style="left:391px;top:672px;width:707px;height:239px">
    <div class="headline" style="left:32px;top:18px;font-size:22px;color:var(--teal-head);font-weight:400">A stay with us<br>Will change your life</div>
    <div class="body" style="left:32px;top:78px;width:290px;font-size:5.4px">
      <p>Velmira, LLC is a research, science and technology based manufacturing company that formulates, develops, manufactures and packages a full complement of personal care products for domestic and international concerns. We private label and contract package personal care products, cosmetics, bath salts and powders and home fragrance products.</p>
      <p>Our strengths are natural and organic product formulation, low minimums, competitive prices, complete research &amp; development services new and innovative ingredients and fast turnaround times.</p>
      <div class="cols" style="font-size:4.6px;margin-top:8px;width:196px">
        <div>
          <div class="cat">Bath &amp; Body Products</div><div class="items">Bath Salts • Body Washes • Body Powders<br>Bath Oils • Bubble Baths</div>
          <div class="cat">Skin Care Products</div><div class="items">Anti-aging Creams • Cleansers • Masks<br>Toners • Serums</div>
          <div class="cat">Manicure / Pedicure</div><div class="items">Cuticle Oils • Sugar • Salt Scrubs<br>Foot Soaks • Softeners</div>
        </div>
        <div>
          <div class="cat">Hair Care Products</div><div class="items">Shampoos • Conditioners • Styling Aids</div>
          <div class="cat">Color Cosmetics</div><div class="items">Eyeliners • Mascaras • Foundations<br>Mineral Make-up Powders</div>
          <div class="cat">Spa Products</div><div class="items">Seaweed Wraps • Cellulite Creams<br>Body Masks • Massage Oils • Candles</div>
        </div>
      </div>
    </div>
    <div class="products" style="left:238px;top:170px;width:82px;height:40px" role="img" aria-label="Spa products: bottles, soaps, towel and flowers"></div>
    <div class="rule" style="left:32px;top:212px;width:300px"></div>
    <div class="address" style="left:32px;top:214px;font-size:5.6px">4120 W. Larkspur Avenue, Building 210, Fullerton, CA 92833.<br><b>P</b> 555.302.4100 &nbsp;|&nbsp; <b>F</b> 555.302.4101 &nbsp;|&nbsp; <b>E</b> info@velmira.com</div>
    <div class="flower" style="left:316px;bottom:0;width:32px;height:28px" role="img" aria-label="Gold hibiscus flower decoration"></div>
    <div class="photo" style="left:348px;width:359px;height:239px" role="img" aria-label="Lab scientist in cap, mask and goggles holding a test tube"></div>
    <div class="brand" style="right:14px;top:10px;font-size:22px"><span class="dot" style="width:9px;height:9px"></span>Velmira</div>
  </section>
</div>
</body>
</html>
```